Australian Trucking Company Requires Professional Looking Stationary

We require a professional looking stationary design that incorporates our newly designed logo.

Our business, called "Brell Haulage Contracting", provides contracting work, transport and logistics to business in Western Australia particularly with links to the mining sector.

We are a small business looking to expand and our new logo and our new stationary will help develop our brand image in our market place.

Target Market(s)

Businesses and Corporation with links to the Mining Sector

Industry/Entity Type

Small Business

Requirements
Must have
• The letterhead must have the following details:
The new logo

Text saying: "Brell Holdings Pty Ltd (ACN 582 316 907) ATF The Brell Discretionary Trust T/AS"
"ABN 71 834 209 553"
Address "P.O Box 817 Wattlegrove WA, 6958"
Phone: 08 9352 7140
Email: brellhaul@mailbox-example.com.au

The text on the letterhead should be editable as the details are likely to change in the near future. Provision should be made for a website address all though one isn't available at the moment.

The styling, layout and font text is entirely up to the designer.

```html
<!DOCTYPE html>
<html lang="en">
<head>
<meta charset="utf-8">
<title>Brell Haulage Contracting — Letterhead</title>
<link rel="stylesheet" href="https://fonts.googleapis.com/css2?family=Open+Sans:wght@400;600;700&display=swap">
<style>
  :root {
    --paper: #ffffff;
    --brand-red: #e31e24;
    --brand-maroon: #8c1015;
    --ink: #5a5a5a;
    --ghost-light: #f6f6f6;
    --ghost-dark: #e4e4e4;
  }
  * { margin: 0; padding: 0; box-sizing: border-box; }
  html, body {
    width: 1018px;
    height: 1200px;
    overflow: hidden;
    background: var(--paper);
  }
  .letterhead {
    position: relative;
    width: 1018px;
    height: 1200px;
    background: var(--paper);
    font-family: "Open Sans", Arial, sans-serif;
    color: var(--ink);
    overflow: hidden;
  }
  .brand {
    position: absolute;
    left: 48px;
    top: 74px;
    display: flex;
    align-items: center;
    gap: 22px;
  }
  .brand-mark {
    width: 110px;
    height: 110px;
    background: var(--brand-maroon);
  }
  .brand-name {
    font-weight: 700;
    font-size: 34px;
    line-height: 1.05;
    text-transform: uppercase;
    letter-spacing: 1px;
    color: var(--brand-maroon);
  }
  .brand-name span { display: block; }
  .ghost-art {
    position: absolute;
    left: 335px;
    top: 670px;
    width: 683px;
    height: 500px;
    background: radial-gradient(ellipse at 60% 55%, var(--ghost-dark) 0%, var(--ghost-light) 55%, rgba(255,255,255,0) 78%);
  }
  .contact {
    position: absolute;
    top: 1125px;
    font-size: 14.5px;
    line-height: 20px;
  }
  .contact-entity { left: 48px; }
  .contact-reach { left: 357px; }
  .label { color: var(--brand-maroon); font-weight: 600; }
  .footer-rule {
    position: absolute;
    left: 0;
    bottom: 0;
    width: 1018px;
    height: 26px;
  }
  .web-address {
    position: absolute;
    right: 28px;
    bottom: 4px;
    font-size: 13px;
    color: #ffffff;
  }
</style>
</head>
<body>
  <main class="letterhead">
    <header class="brand">
      <div class="brand-mark"></div>
      <h1 class="brand-name"><span>Brell</span><span>Haulage</span><span>Contracting</span></h1>
    </header>

    <div class="ghost-art" role="img" aria-label="Faint oversized brand emblem decoration in pale grey"></div>

    <footer>
      <address class="contact contact-entity">
        <span class="label">Brell Holdings Pty Ltd</span>&nbsp; (ACN 582 316 907)<br>
        ATF The Brell Discretionary Trust T/AS<br>
        <span class="label">ABN</span> 71 834 209 553
      </address>
      <address class="contact contact-reach">
        P.O Box 817 Wattlegrove WA, 6958<br>
        <span class="label">P.</span> 08 9352 7140<br>
        <span class="label">E.</span> brellhaul@mailbox-example.com.au
      </address>

      <svg class="footer-rule" viewBox="0 0 1018 26" aria-hidden="true">
        <rect x="0" y="13" width="1018" height="8" fill="var(--brand-maroon)"/>
        <polygon points="742,0 1018,0 1018,26 726,26" fill="var(--brand-red)"/>
      </svg>
      <span class="web-address">www.brellhaulage-example.com.au</span>
    </footer>
  </main>
</body>
</html>
```